TWPC Business Card Design

Business card for sole operator professional civil and traffic engineer.
Clients are developers and planners who require assistance with traffic strategic master planning advice and design development for access and infrastructure associated with the development.
Colours already in use are greens for the business name and black for other legend. The attached file shows the letterhead template which is currently in use.
Target Market(s)
Professional Clients in development industry
Most clients known to the Principal and card is mostly required to allow ongoing contact
Industry/Entity Type
Business
Contact Information for Business Card
LACHLAN PETTIGREW CONSULTING PARTNERS
ABN 37 814 529 106
PO Box 418 KELWOOD NSW 2619
Lachlan Pettigrew 0412 358 971
l.pettigrew@corvanmail.net

```html
<!DOCTYPE html>
<html lang="en">
<head>
<meta charset="utf-8">
<title>TWPC Business Card</title>
<link rel="stylesheet" href="https://fonts.googleapis.com/css2?family=Lato:wght@400;700;900&display=swap">
<style>
  :root {
    --page-bg: #e9e9e6;
    --brand-green: #9aca3c;
    --ink: #111111;
    --paper-light: #f4f4f4;
    --paper-mid: #cfcfcf;
    --paper-dark: #8e8e8e;
  }
  * { margin: 0; padding: 0; box-sizing: border-box; }
  html, body {
    width: 1200px;
    height: 841px;
    overflow: hidden;
    background: var(--page-bg);
    font-family: "Lato", Arial, sans-serif;
  }
  .canvas {
    position: relative;
    width: 1200px;
    height: 841px;
  }
  .business-card {
    position: absolute;
    left: 100px;
    top: 115px;
    width: 1000px;
    height: 611px;
    overflow: hidden;
    box-shadow: 0 10px 30px rgba(0,0,0,0.18);
  }
  .blueprint-backdrop {
    position: absolute;
    inset: 0;
    background: linear-gradient(115deg, var(--paper-dark) 0%, var(--paper-mid) 30%, var(--paper-light) 55%, var(--paper-mid) 80%, var(--paper-light) 100%);
  }
  .info-band {
    position: absolute;
    left: 0;
    right: 0;
    top: 132px;
    height: 345px;
    background: var(--brand-green);
    color: var(--ink);
    text-align: center;
    padding-top: 34px;
  }
  .company-name {
    font-weight: 900;
    font-size: 36px;
    line-height: 1.15;
    letter-spacing: -0.3px;
  }
  .company-abn,
  .postal-address {
    font-weight: 900;
    font-size: 30px;
    line-height: 1.2;
  }
  .principal-name {
    margin-top: 14px;
    font-size: 50px;
    line-height: 1.1;
    font-weight: 400;
  }
  .principal-name .surname { font-weight: 900; }
  .contact-line {
    margin-top: 22px;
    font-size: 27px;
    font-weight: 400;
  }
  .contact-line .divider { margin: 0 10px; }
</style>
</head>
<body>
<div class="canvas">
  <div class="business-card">
    <div class="blueprint-backdrop" role="img" aria-label="Photograph of rolled architectural blueprints and plan drawings in grey tones"></div>
    <div class="info-band">
      <div class="company-name">LACHLAN PETTIGREW CONSULTING PARTNERS</div>
      <div class="company-abn">ABN 37 814 529 106</div>
      <div class="postal-address">PO Box 418 KELWOOD NSW 2619</div>
      <div class="principal-name">LACHLAN <span class="surname">PETTIGREW</span></div>
      <div class="contact-line">PHONE: 0412 358 971<span class="divider">|</span>EMAIL: l.pettigrew@corvanmail.net</div>
    </div>
  </div>
</div>
</body>
</html>
```